Venture Capital Investment Firm

We are looking to overhaul our existing website (substantially), with only using the same logos (which we can provide).
We are an investment firm that focuses on making loans to late stage technology companies. Our site should ultimately look like other venture capital firms, and look modern and fresh. We have an existing website www.norvellhub.com which this will be replacing, although we will be using a lot of the existing written content, and potentially the numbers of pages we will need, we are not wed to anything else. Please feel free to shoot any questions at any time and thank you in advance for your help!
Websites we like as examples:
https://www.tesmarkfund.com/
https://www.brindlewoodpartners.com/
Target Market(s)
Potential investors who will invest in our firm, as well as potentially companies that are looking to borrow money from us.
Coding
Coded - Design and coding required
Number of Pages Required
5+ page
Colors
Designer to choose colors to be used in the design.
Look and feel

```html
<!DOCTYPE html>
<html lang="en">
<head>
<meta charset="utf-8">
<title>Norvell IP — Investment Partners</title>
<link href="https://fonts.googleapis.com/css2?family=Barlow:ital,wght@0,400;0,500;0,600;0,700;1,500&display=swap" rel="stylesheet">
<style>
:root{
  --navy:#141838;
  --navy-deep:#0e1230;
  --blue:#1a8fd0;
  --sky:#4fa7d8;
  --ink:#1d1f2e;
  --body:#555a66;
  --line:#e3e6ec;
  --paper:#ffffff;
  --mist:#f1f2f5;
}
*{margin:0;padding:0;box-sizing:border-box}
html,body{width:1200px;height:4777px;overflow:hidden;background:var(--paper)}
body{font-family:'Barlow',sans-serif;color:var(--body);position:relative}
.abs{position:absolute}
.topbar{left:0;top:0;width:1200px;height:34px;background:var(--navy);color:#fff;font-size:15px;display:flex;align-items:center;justify-content:flex-end;padding-right:155px;gap:38px}
.topbar span{display:flex;align-items:center;gap:8px}
.social{display:flex;gap:5px}
.social i{width:24px;height:24px;border:1.5px solid currentColor;border-radius:50%;display:block}
.header{left:0;top:34px;width:1200px;height:92px;border-bottom:1px solid var(--line);display:flex;align-items:center;padding-left:143px}
.brand{display:flex;align-items:center;gap:12px;font-size:34px;font-weight:500;color:var(--ink);letter-spacing:.5px}
.brand i{width:42px;height:42px;border-radius:50%;background:var(--navy);display:block}
.nav{display:flex;gap:28px;margin-left:60px;font-size:15px;font-weight:600;color:var(--ink)}
.nav a{position:relative}
.nav a.on:after{content:"";position:absolute;left:0;right:0;top:46px;height:3px;background:var(--navy)}
.hero{left:0;top:126px;width:1200px;height:600px;background:linear-gradient(90deg,#101633 0%,#172650 55%,#2b4a78 100%)}
.hero h1{position:absolute;left:143px;top:160px;font-size:58px;font-weight:600;color:#fff}
.hero p{position:absolute;left:143px;top:244px;width:330px;font-size:19px;font-weight:600;line-height:31px;color:#fff}
.btn{display:inline-block;padding:11px 26px;font-size:15px;font-weight:700;text-transform:uppercase;position:absolute;box-shadow:6px 0 0 -2px currentColor}
.btn.light{background:#fff;color:var(--navy)}
.btn.dark{background:var(--navy);color:#fff;box-shadow:7px 0 0 -3px var(--navy)}
.hero .btn{left:143px;top:366px}
.dots{display:flex;gap:14px}
.dots i{width:16px;height:16px;border-radius:50%;border:2px solid #fff;display:block}
.dots i.on{background:var(--sky);border-color:var(--sky)}
.welcome-img{left:146px;top:800px;width:373px;height:373px;border-radius:50%;background:radial-gradient(circle,#e7e9ee,#9aa0ab)}
.welcome h2{position:absolute;left:588px;top:812px;font-size:42px;font-weight:400;color:var(--ink)}
.welcome h2 b{font-weight:700}
.welcome h2:after{content:"";position:absolute;left:0;top:60px;width:200px;height:2px;background:var(--ink)}
.welcome p{position:absolute;left:588px;top:905px;width:470px;font-size:15px;line-height:31.5px}
.welcome .btn{left:588px;top:1117px}
.panel{top:1258px;width:300px;height:532px}
.panel.photo{background:linear-gradient(160deg,#5a6f8e,#1f2c49)}
.panel.blue{background:var(--blue);color:#fff;text-align:center;padding:0 22px}
.panel svg{margin-top:85px}
.panel h3{font-size:24px;font-weight:600;margin-top:22px;text-transform:uppercase}
.panel p{font-size:14.5px;line-height:25.5px;margin-top:12px}
.panel .btn{position:relative;margin-top:28px}
.strategy{left:0;top:1790px;width:1200px;height:532px;background:linear-gradient(120deg,#1d2440,#3b4a68 60%,#8692a8)}
.strategy h2{position:absolute;left:0;width:1200px;top:130px;text-align:center;color:#fff;font-size:33px;font-weight:700;line-height:46px;text-transform:uppercase}
.strategy .rule{position:absolute;left:558px;top:294px;width:84px;height:3px;background:#fff}
.strategy .btn{left:445px;top:336px;font-size:14px}
.sec-title{position:absolute;left:0;width:1200px;text-align:center;color:var(--ink);font-size:38px;font-weight:700;text-transform:uppercase}
.sec-title:after{content:"";display:block;width:70px;height:3px;background:var(--sky);margin:20px auto 0}
.lead{left:180px;top:2505px;width:840px;text-align:center;font-size:15px;line-height:27px}
.benefit{top:2638px;width:292px;height:340px;text-align:center;padding-top:44px}
.benefit.raised{background:#fff;box-shadow:0 4px 18px rgba(0,0,0,.14)}
.benefit .ico{width:92px;height:92px;border-radius:50%;background:var(--sky);margin:0 auto}
.benefit.raised .ico{background:var(--navy)}
.benefit h4{font-size:18px;font-weight:600;color:var(--ink);margin-top:40px}
.benefit p{font-size:15px;line-height:25.5px;margin:14px 28px 0}
.clients{left:0;top:3070px;width:1200px;height:650px}
.quote{top:3307px;width:287px;height:273px;background:#fff;text-align:center;padding:22px 20px 0;border-top:3px solid var(--sky);border-left:3px solid var(--sky)}
.quote .mark{font-size:70px;line-height:52px;font-weight:700;color:var(--sky);font-family:Georgia,serif}
.quote p{font-size:13.5px;line-height:25px;margin-top:12px}
.quote .rule{width:56px;height:2px;background:var(--sky);margin:8px auto 14px}
.quote em{font-size:14.5px;font-weight:500;color:var(--ink)}
.news{top:3916px;width:448px;height:274px;border:1px solid #d6d9df;border-radius:4px;background:#fff;display:flex;overflow:hidden}
.news .pic{width:228px;height:100%;background:linear-gradient(150deg,#c9ccd2,#59647a)}
.news .body{padding:30px 0 0 22px;width:220px}
.news h5{font-size:20px;font-weight:400;color:var(--ink);line-height:27px}
.news .date{display:inline-block;border:1.5px solid var(--blue);color:var(--blue);font-size:12px;font-weight:600;padding:4px 10px;margin:14px 0 18px}
.news p{font-size:13px;line-height:24px}
.footer{left:0;top:4294px;width:1200px;height:381px;background:var(--mist)}
.footer h6{font-size:18px;font-weight:500;color:var(--ink);text-transform:uppercase;position:absolute}
.footer .txt{position:absolute;font-size:13.5px;line-height:22px}
.input{position:absolute;left:374px;top:4485px;width:272px;height:38px;border:1px solid #cfd3da;border-radius:19px;background:#fff;font-size:11px;padding:12px 14px;color:#777}
.sub{position:absolute;left:374px;top:4537px;width:114px;height:36px;border-radius:18px;background:var(--blue);color:#fff;font-size:13px;font-weight:600;text-align:center;line-height:36px}
.links{position:absolute;left:952px;top:4430px;font-size:13.5px;line-height:27px}
.copy{left:0;top:4717px;width:1200px;text-align:center;font-size:12.5px;color:var(--ink)}
</style>
</head>
<body>

<div class="abs topbar">
  <span><svg width="14" height="14" viewBox="0 0 24 24"><path fill="#fff" d="M6.6 10.8a15 15 0 0 0 6.6 6.6l2.2-2.2c.3-.3.7-.4 1-.2 1.1.4 2.3.6 3.6.6.6 0 1 .4 1 1V20c0 .6-.4 1-1 1C10.6 21 3 13.4 3 4c0-.6.4-1 1-1h3.5c.6 0 1 .4 1 1 0 1.3.2 2.5.6 3.6.1.3 0 .7-.2 1z"/></svg>+808 5550 1400</span>
  <span><svg width="16" height="12" viewBox="0 0 16 12"><rect width="16" height="12" rx="1" fill="#fff"/><path d="M0 1l8 6 8-6" stroke="#141838" stroke-width="1.5" fill="none"/></svg>inquiries@norvellhub.com</span>
  <span class="social"><i></i><i></i><i></i></span>
</div>

<header class="abs header">
  <div class="brand"><i></i>Norvell IP</div>
  <nav class="nav"><a class="on">HOME</a><a>STRATEGY</a><a>ABOUT</a><a>TEAM</a><a>NEWS</a><a>INVESTORS</a><a>CONTACT</a></nav>
</header>

<section class="abs hero">
  <div class="abs" style="left:0;top:0;width:1200px;height:600px" role="img" aria-label="Woman using a tablet beside a glowing network of finance and technology icons"></div>
  <h1>Norvell IP</h1>
  <p>We Are A Global Structured Credit Investment Firm Focused On The Healthcare And Technology Industries</p>
  <a class="btn light">Read More</a>
  <div class="abs dots" style="left:560px;top:536px"><i class="on"></i><i></i><i></i></div>
  <svg class="abs" style="left:0;top:580px" width="1200" height="22" viewBox="0 0 1200 22" preserveAspectRatio="none"><path fill="#fff" d="M0 12 Q10 0 20 12 T40 12 T60 12 T80 12 T100 12 T120 12 T140 12 T160 12 T180 12 T200 12 T220 12 T240 12 T260 12 T280 12 T300 12 T320 12 T340 12 T360 12 T380 12 T400 12 T420 12 T440 12 T460 12 T480 12 T500 12 T520 12 T540 12 T560 12 T580 12 T600 12 T620 12 T640 12 T660 12 T680 12 T700 12 T720 12 T740 12 T760 12 T780 12 T800 12 T820 12 T840 12 T860 12 T880 12 T900 12 T920 12 T940 12 T960 12 T980 12 T1000 12 T1020 12 T1040 12 T1060 12 T1080 12 T1100 12 T1120 12 T1140 12 T1160 12 T1180 12 T1200 12 V22 H0Z"/></svg>
</section>

<section class="welcome">
  <div class="abs welcome-img" role="img" aria-label="Circular collage of office and finance photographs"></div>
  <h2>Welcome to <b>Norvell IP</b></h2>
  <p>Norvell IP is a private investment firm unique in its dual focus on life science and technology credit opportunities. Our ambidextrous approach to investing reflects a broad recognition and appreciation for the critical role intellectual property plays in the successful commercialization of products. We apply our extensive industry expertise to assess the revenue visibility created</p>
  <a class="btn dark">Read More</a>
</section>

<div class="abs panel photo" style="left:0" role="img" aria-label="Scientist thinking beside hexagonal life science icons"></div>
<div class="abs panel blue" style="left:300px">
  <svg width="66" height="72" viewBox="0 0 66 72" fill="none" stroke="#fff" stroke-width="2"><circle cx="33" cy="28" r="20"/><path d="M25 48v10h16V48M27 64h12"/><path d="M33 14v28M23 28h20"/></svg>
  <h3>Life Sciences</h3>
  <p>We have a long track record of partnering with companies and investors that create and commercialize life science products, with extensive experience spanning biopharmaceuticals</p>
  <a class="btn dark">Read More</a>
</div>
<div class="abs panel photo" style="left:600px;background:linear-gradient(170deg,#6d7d95,#15203a)" role="img" aria-label="Hand holding a smartphone over glowing financial charts"></div>
<div class="abs panel blue" style="left:900px">
  <svg width="76" height="72" viewBox="0 0 76 72" fill="none" stroke="#fff" stroke-width="2"><rect x="6" y="16" width="64" height="42" rx="3"/><path d="M2 62h72M14 48l12-12 10 8 14-16 12 8"/><circle cx="48" cy="14" r="10"/></svg>
  <h3>Technology</h3>
  <p>We uniquely offer sizeable and flexible structured credit financing solutions to innovative technology companies, with a focus on enterprise software, data &amp; analytics, semiconductors, and communications systems.</p>
  <a class="btn dark">Read More</a>
</div>
<svg class="abs" style="left:0;top:1250px" width="1200" height="18" viewBox="0 0 1200 18" preserveAspectRatio="none"><path fill="#fff" d="M0 0H1200V8 Q1190 16 1180 8 T1160 8 T1140 8 T1120 8 T1100 8 T1080 8 T1060 8 T1040 8 T1020 8 T1000 8 T980 8 T960 8 T940 8 T920 8 T900 8 T880 8 T860 8 T840 8 T820 8 T800 8 T780 8 T760 8 T740 8 T720 8 T700 8 T680 8 T660 8 T640 8 T620 8 T600 8 T580 8 T560 8 T540 8 T520 8 T500 8 T480 8 T460 8 T440 8 T420 8 T400 8 T380 8 T360 8 T340 8 T320 8 T300 8 T280 8 T260 8 T240 8 T220 8 T200 8 T180 8 T160 8 T140 8 T120 8 T100 8 T80 8 T60 8 T40 8 T20 8 T0 8Z"/></svg>

<section class="abs strategy" role="img" aria-label="Desk with calculator and printed pie and bar chart reports">
  <h2>We are a global structured<br>credit investment firm focused on the<br>healthcare and technology industries</h2>
  <div class="rule"></div>
  <a class="btn light">Learn more about our strategy</a>
</section>

<h2 class="sec-title" style="top:2402px">Key Benefits</h2>
<p class="abs lead">We seek to fill a void in the capital markets where too often complexity and perceived risk penalize innovative companies with proven products. We apply our team's deep domain knowledge to identify situations where our structured financing alternatives can deliver a lower cost of capital than traditional venture capital</p>

<div class="abs benefit" style="left:139px"><div class="ico"></div><h4>STRUCTURED CREDIT</h4><p>We offer revenue-generating companies in the life science and technology industries bespoke loans which offer multiple benefits</p></div>
<div class="abs benefit raised" style="left:454px"><div class="ico"></div><h4>MILESTONES &amp; ROYALTIES</h4><p>We offer owners of milestones and royalty rights the ability to monetize or securitize future cash flows ranging from $10-250M.</p></div>
<div class="abs benefit" style="left:769px"><div class="ico"></div><h4>LEGACY ASSETS</h4><p>We offer companies with mature, "non-core" assets upfront capital in exchange for products that are no longer strategic to their businesses.</p></div>

<svg class="abs clients" width="1200" height="650" viewBox="0 0 1200 650"><defs><linearGradient id="nv" x1="0" y1="0" x2="1" y2="1"><stop offset="0" stop-color="#1c2050"/><stop offset="1" stop-color="#141838"/></linearGradient></defs><path d="M0 50L600 0L1200 50V650H0Z" fill="url(#nv)"/><path d="M0 50L600 0L1200 50" stroke="#4fa7d8" stroke-width="4" fill="none"/></svg>
<h2 class="sec-title" style="top:3177px;color:#fff">What our clients's say</h2>
<div class="abs quote" style="left:134px"><div class="mark">“</div><p>Sed ut perspiciatis unde omnis iste natus error sit voluptatem accusantium doloremque laudantium, totam rem aperiam, eaque ipsa quae ab illo inventore veritatis et</p><div class="rule"></div><em>Nemo enim ipsam - Norvell IP</em></div>
<div class="abs quote" style="left:458px"><div class="mark">“</div><p>Sed ut perspiciatis unde omnis iste natus error sit voluptatem accusantium doloremque laudantium, totam rem aperiam, eaque ipsa quae ab illo inventore veritatis et</p><div class="rule"></div><em>Nemo enim ipsam - Norvell IP</em></div>
<div class="abs quote" style="left:783px"><div class="mark">“</div><p>Sed ut perspiciatis unde omnis iste natus error sit voluptatem accusantium doloremque laudantium, totam rem aperiam, eaque ipsa quae ab illo inventore veritatis et</p><div class="rule"></div><em>Nemo enim ipsam - Norvell IP</em></div>
<div class="abs dots" style="left:568px;top:3632px"><i class="on"></i><i style="background:#fff"></i><i style="background:#fff"></i></div>

<h2 class="sec-title" style="top:3784px">Norvell IP News</h2>
<article class="abs news" style="left:143px"><div class="pic" role="img" aria-label="Person reviewing a business report at a desk"></div><div class="body"><h5>Nemo enim ipsam voluptatem quia volu</h5><span class="date">▣ OCT 17, 2019</span><p>Nemo enim ipsam vtatem quia votas sit aspernatur aut odit aut fugit, sed quia cotur magni dolores eos</p></div></article>
<article class="abs news" style="left:608px"><div class="pic" style="background:linear-gradient(150deg,#d4d7dc,#6c7890)" role="img" aria-label="Analyst viewing charts on a monitor in a city office"></div><div class="body"><h5>Nemo enim ipsam voluptatem quia volu</h5><span class="date">▣ OCT 17, 2019</span><p>Nemo enim ipsam vtatem quia votas sit aspernatur aut odit aut fugit, sed quia cotur magni dolores eos</p></div></article>

<footer class="abs footer">
  <svg class="abs" style="left:0;top:-8px" width="1200" height="16" viewBox="0 0 1200 16" preserveAspectRatio="none"><path fill="#f1f2f5" d="M0 8 Q10 0 20 8 T40 8 T60 8 T80 8 T100 8 T120 8 T140 8 T160 8 T180 8 T200 8 T220 8 T240 8 T260 8 T280 8 T300 8 T320 8 T340 8 T360 8 T380 8 T400 8 T420 8 T440 8 T460 8 T480 8 T500 8 T520 8 T540 8 T560 8 T580 8 T600 8 T620 8 T640 8 T660 8 T680 8 T700 8 T720 8 T740 8 T760 8 T780 8 T800 8 T820 8 T840 8 T860 8 T880 8 T900 8 T920 8 T940 8 T960 8 T980 8 T1000 8 T1020 8 T1040 8 T1060 8 T1080 8 T1100 8 T1120 8 T1140 8 T1160 8 T1180 8 T1200 8 V16 H0Z"/></svg>
  <div class="brand abs" style="left:143px;top:96px;font-size:27px"><i style="width:34px;height:34px"></i>Norvell IP</div>
  <div class="abs social" style="left:143px;top:150px;color:var(--ink)"><i style="width:28px;height:28px"></i><i style="width:28px;height:28px"></i><i style="width:28px;height:28px"></i><i style="width:28px;height:28px"></i></div>
  <h6 style="left:374px;top:90px">Sign up for newsletter</h6>
  <p class="txt" style="left:374px;top:130px;width:290px">Excepteur sint occaecat cupidatat non proident, sunt in culpa qui officia deserunt</p>
  <h6 style="left:687px;top:92px">Contact us</h6>
  <svg class="abs" style="left:690px;top:134px" width="16" height="20" viewBox="0 0 16 20"><path fill="#1a8fd0" d="M8 0a7 7 0 0 0-7 7c0 5 7 13 7 13s7-8 7-13a7 7 0 0 0-7-7zm0 10a3 3 0 1 1 0-6 3 3 0 0 1 0 6z"/></svg>
  <p class="txt" style="left:724px;top:130px">Norvell IP<br>2200 Harlow Street #318<br>Oakland, CA 94607</p>
  <svg class="abs" style="left:690px;top:220px" width="16" height="16" viewBox="0 0 24 24"><path fill="#1a8fd0" d="M6.6 10.8a15 15 0 0 0 6.6 6.6l2.2-2.2c.3-.3.7-.4 1-.2 1.1.4 2.3.6 3.6.6.6 0 1 .4 1 1V20c0 .6-.4 1-1 1C10.6 21 3 13.4 3 4c0-.6.4-1 1-1h3.5c.6 0 1 .4 1 1 0 1.3.2 2.5.6 3.6.1.3 0 .7-.2 1z"/></svg>
  <p class="txt" style="left:724px;top:216px">Phone:<br>1300-5540-2271</p>
  <svg class="abs" style="left:690px;top:272px" width="16" height="12" viewBox="0 0 16 12"><rect width="16" height="12" rx="1" fill="#1a8fd0"/><path d="M0 1l8 6 8-6" stroke="#f1f2f5" stroke-width="1.5" fill="none"/></svg>
  <p class="txt" style="left:724px;top:268px">Email:<br>inquiries@norvellhub.com</p>
  <h6 style="left:948px;top:90px">Quick links</h6>
</footer>
<div class="input">Enter email</div>
<div class="sub">SUBSCRIBE</div>
<div class="links">Home<br>Strategy<br>About Us<br>Team<br>News<br>Contact<br>Investors</div>
<p class="abs copy">Norvell IP © 2019 All Rights Reserved | Privacy Policy | Terms and Conditions</p>

</body>
</html>
```